Insurance Agency website design for Brellow Cover Insurance, LP

Build a website for Brellow Cover Insurance, LP which sells Homeowners, Auto, Renters, Condo, Flood, Disability, Life, Umbrella, and health insurance. We need the coolest insurance agency website out there to get quotes, contact us, or get additional information. Please list the following insurance companies we work with: Varnix, Ostle, Meridale Mutual, Quillor, Dunmarrow, KGZ, and Pellwick.

Make a design similar to https://www.fernagentry.com/

Selling personal insurance policies

```html
<!DOCTYPE html>
<html lang="en">
<head>
<meta charset="utf-8">
<title>Brellow Cover Insurance, LP</title>
<link href="https://fonts.googleapis.com/css2?family=Jost:wght@400;500;600;700&family=Montserrat:wght@400;700;800&display=swap" rel="stylesheet">
<style>
:root{
  --navy:#1b3c8a;
  --navy-deep:#172f7c;
  --band:#2a5298;
  --green:#7dbf41;
  --green-dark:#5ea62c;
  --ink:#1c1c1c;
  --muted:#6f6f6f;
  --light:#f4f6f9;
  --footer:#121212;
  --white:#fff;
}
*{box-sizing:border-box;margin:0;padding:0}
html,body{width:1200px;height:3496px;overflow:hidden}
body{font-family:"Jost",sans-serif;color:var(--ink);background:var(--white);position:relative}
.abs{position:absolute}
a{color:inherit;text-decoration:none}

/* header */
.topbar{left:650px;top:0;width:550px;height:27px;background:var(--green);clip-path:polygon(26px 0,100% 0,100% 100%,0 100%);color:#fff;font-size:12px;display:flex;align-items:center;justify-content:flex-end;gap:26px;padding-right:58px}
.topbar span{display:flex;align-items:center;gap:6px}
.header{left:0;top:27px;width:1200px;height:71px}
.brand{left:105px;top:34px;display:flex;align-items:center;gap:8px;font-weight:600;font-size:15px;color:var(--navy)}
.brand .mark{width:18px;height:18px;background:var(--green)}
.nav{left:310px;top:50px;display:flex;gap:40px;font-size:13.5px;font-weight:500;color:#222}
.btn{display:inline-flex;align-items:center;justify-content:center;gap:10px;border-radius:4px;color:#fff;font-weight:500}
.header-cta{left:961px;top:38px;width:133px;height:40px;background:var(--navy);font-size:15px}

/* hero */
.hero-photo{left:0;top:98px;width:1200px;height:590px;background:linear-gradient(100deg,#23539a 0%,#3b6aa8 50%,#7f95b4 100%)}
.hero-curve{left:0;top:600px;width:1200px;height:110px}
.hero-title{left:140px;top:205px;color:#fff;font-family:"Montserrat",sans-serif;font-size:44px;line-height:55px}
.hero-title b{font-weight:800}
.hero-title span{font-weight:400}
.hero-text{left:140px;top:385px;width:510px;color:#fff;font-size:15px;line-height:21px}
.hero-cta{left:140px;top:470px;width:205px;height:44px;background:var(--green);font-size:15px;border-radius:2px}
.scroll{left:565px;top:692px;width:70px;height:70px;border-radius:50%;background:#fff;box-shadow:0 4px 14px rgba(0,0,0,.12);display:flex;align-items:center;justify-content:center}

/* about */
.about-photo{left:141px;top:856px;width:423px;height:415px;background:linear-gradient(135deg,#b9b3aa,#8d8f92 60%,#d8d5d0);border-radius:22px;clip-path:polygon(0 0,80% 0,80% 12%,100% 12%,100% 100%,17% 100%,17% 88%,0 88%)}
.stat{left:419px;top:1197px;width:177px;height:119px;background:var(--green);border-radius:10px;outline:6px solid #fff;color:#fff;text-align:center;padding-top:10px}
.stat strong{display:block;font-size:42px;font-weight:600;line-height:44px}
.stat span{font-size:18px;line-height:22px;display:block}
.tag{left:643px;top:864px;padding:3px 10px;background:#e3efd9;color:#435a35;font-size:13px;letter-spacing:1.5px;border-radius:3px}
.about-title{left:643px;top:898px;font-size:28px;font-weight:600;color:#1f1f1f}
.about-copy{left:643px;top:950px;width:415px;font-size:15px;line-height:21.3px;color:#333}
.about-copy p{margin-bottom:6px}
.read-more{left:643px;top:1261px;width:135px;height:42px;background:var(--navy);font-size:15px;letter-spacing:.5px;border-radius:2px}

/* types */
.types{left:0;top:1409px;width:1200px;height:792px;background:linear-gradient(180deg,#1f4c8f,#2d5c9f 55%,#2a5a9d)}
.types h2{position:absolute;top:86px;width:100%;text-align:center;color:#fff;font-size:30px;font-weight:600}
.card{width:246px;height:228px;background:#fff;border-radius:4px;text-align:center;padding:22px 18px 0}
.card .ico{width:56px;height:56px;margin:0 auto 12px;border-radius:6px;display:flex;align-items:center;justify-content:center}
.ico.blue{background:#dbe6f4}.ico.green{background:#dcefcf}
.card h3{font-size:19px;font-weight:500;margin-bottom:9px}
.card p{font-size:12.2px;line-height:19px;color:var(--muted)}
.explore{left:523px;top:2091px;width:154px;height:41px;background:var(--green);font-size:15px;border-radius:2px}

/* partners */
.partners-title{left:0;top:2272px;width:1200px;text-align:center;font-size:30px;font-weight:600}
.logo{width:160px;height:118px;background:#fff;box-shadow:0 2px 10px rgba(0,0,0,.1);display:flex;align-items:center;justify-content:center;font-size:20px;font-weight:600;color:#1f3c78}

/* quote */
.quote{left:141px;top:2689px;width:918px;height:319px;background:linear-gradient(135deg,#1d3a90,#1e3486);border-radius:6px;color:#fff;text-align:center}
.quote h2{margin-top:75px;font-size:30px;font-weight:600}
.quote p{width:530px;margin:10px auto 0;font-size:15.5px;line-height:21px}
.quote .btn{margin-top:16px;width:154px;height:41px;background:var(--green);font-size:15px;letter-spacing:.5px;border-radius:2px}

/* footer */
.footer{left:0;top:3094px;width:1200px;height:361px;background:var(--footer);color:#ddd}
.f-col{position:absolute;top:84px}
.f-col h4{font-size:16.5px;font-weight:500;color:#fff;margin-bottom:18px}
.f-about{left:142px;top:88px;width:310px}
.f-about h4{font-size:21px;font-weight:600}
.f-about p{font-size:13.5px;line-height:21px}
.f-about a{text-decoration:underline}
.f-col ul{list-style:none;font-size:13.5px}
.links li{margin-bottom:11px}
.links li::before{content:"»";margin-right:8px}
.social li{display:flex;align-items:center;gap:8px;margin-bottom:12px}
.social i{width:28px;height:28px;border:1.5px solid #ddd;border-radius:50%}
.contact li{display:flex;gap:12px;margin-bottom:14px;line-height:19px}
.copyright{left:0;top:3455px;width:1200px;height:41px;background:var(--navy);color:#fff;font-size:12px;display:flex;align-items:center;justify-content:center}
</style>
</head>
<body>

<div class="abs topbar">
  <span><svg width="11" height="11" viewBox="0 0 24 24" fill="#fff"><path d="M6.6 10.8a15 15 0 006.6 6.6l2.2-2.2a1 1 0 011-.25 11.4 11.4 0 003.6.57 1 1 0 011 1V20a1 1 0 01-1 1A17 17 0 013 4a1 1 0 011-1h3.5a1 1 0 011 1c0 1.25.2 2.45.57 3.57a1 1 0 01-.25 1z"/></svg>Phone: 123-456-7890</span>
  <span><svg width="12" height="10" viewBox="0 0 24 20" fill="#fff"><path d="M2 0h20a2 2 0 012 2v16a2 2 0 01-2 2H2a2 2 0 01-2-2V2a2 2 0 012-2zm10 9L2 3v2l10 6 10-6V3z"/></svg>E-Mail: info@brellowcover.com</span>
</div>
<header class="abs header">
  <div class="abs brand" style="left:105px;top:34px;position:absolute"><span class="mark"></span>Brellow Cover</div>
  <nav class="abs nav" style="top:23px">
    <a>HOME</a><a>ABOUT US</a><a>INSURANCE ⌄</a><a>MARKET PARTNERS</a><a>CONTACT</a>
  </nav>
  <a class="abs btn header-cta" style="top:11px">Get a Quote</a>
</header>

<section>
  <div class="abs hero-photo" role="img" aria-label="Young family sitting among moving boxes, father holding a cardboard roof over them"></div>
  <svg class="abs hero-curve" viewBox="0 0 1200 110" preserveAspectRatio="none">
    <path d="M0 10 L600 95 L1200 0 L1200 110 L0 110Z" fill="#fff"/>
    <path d="M0 10 L600 95 L1200 0 L1200 22 L600 110 L0 35Z" fill="var(--green)"/>
    <path d="M0 35 L600 110 L1200 22 L1200 110 L0 110Z" fill="#fff"/>
  </svg>
  <h1 class="abs hero-title"><b>Protect What Matters</b><br><span>Most with Trusted</span><br><b>Insurance</b></h1>
  <p class="abs hero-text">At Brellow Cover Insurance, we understand how crucial it is to protect the things that matter most to you - your home, health, and family.</p>
  <a class="abs btn hero-cta">Get Your Quote Now</a>
  <div class="abs scroll"><svg width="16" height="26" viewBox="0 0 16 26" fill="none" stroke="var(--navy)" stroke-width="1.8"><rect x="1" y="1" width="14" height="24" rx="7"/><line x1="8" y1="6" x2="8" y2="11"/></svg></div>
</section>

<section>
  <div class="abs about-photo" role="img" aria-label="Insurance advisor meeting with an older couple at a table with a laptop"></div>
  <div class="abs stat"><strong>50+</strong><span>Skilled<br>Professionals</span></div>
  <span class="abs tag">About Us</span>
  <h2 class="abs about-title">BRELLOW COVER INSURANCE</h2>
  <div class="abs about-copy">
    <p>Brellow Cover Insurance is a full-service, independent insurance agency with over three decades of experience in delivering comprehensive insurance solutions to individuals.</p>
    <p>We proudly offer a diverse portfolio of products from more than 20 of the most reputable and financially secure companies in the industry. Our dedicated team of over 50 skilled professionals is committed to customizing these products and services to meet the unique needs of each client.</p>
    <p>At Brellow Cover Insurance, our experts are focused on addressing the individual needs of our clients, ensuring exceptional service and support at every step.</p>
  </div>
  <a class="abs btn read-more">Read More <span>↗</span></a>
</section>

<section class="abs types">
  <h2>INSURANCE TYPES</h2>
  <div class="abs card" style="left:75px;top:161px"><div class="ico blue"><svg width="30" height="30" viewBox="0 0 24 24" fill="none" stroke="var(--navy)" stroke-width="2"><path d="M3 11l9-7 9 7v9H3z"/></svg></div><h3>Homeowners</h3><p>Protect your home and belongings from damage, theft, or disaster with comprehensive homeowners coverage.</p></div>
  <div class="abs card" style="left:343px;top:161px"><div class="ico green"><svg width="30" height="30" viewBox="0 0 24 24" fill="var(--green-dark)"><path d="M5 11l2-5h10l2 5v7h-2v-2H7v2H5z"/></svg></div><h3>Auto Insurance</h3><p>Safeguard your vehicle against accidents, theft, or damage, ensuring you're covered on the road.</p></div>
  <div class="abs card" style="left:611px;top:161px"><div class="ico blue"><svg width="30" height="30" viewBox="0 0 24 24" fill="none" stroke="var(--navy)" stroke-width="2"><path d="M4 10l8-5 8 5M6 10v9h12v-9"/></svg></div><h3>Renters Insurance</h3><p>Protect personal belongings in a rental space, covering damage, theft, or loss due to disasters.</p></div>
  <div class="abs card" style="left:879px;top:161px"><div class="ico green"><svg width="30" height="30" viewBox="0 0 24 24" fill="var(--green-dark)"><path d="M6 3h12v18H6z"/></svg></div><h3>Condo Insurance</h3><p>Cover your condo unit and personal property, filling the gap not covered by the building's insurance.</p></div>
  <div class="abs card" style="left:75px;top:411px"><div class="ico green"><svg width="30" height="30" viewBox="0 0 24 24" fill="none" stroke="var(--green-dark)" stroke-width="2"><path d="M4 12l8-6 8 6v6H4zM2 21c3-2 5 2 10 0s7 2 10 0"/></svg></div><h3>Flood Insurance</h3><p>Provide financial protection against water damage caused by floods, which are often excluded from standard coverage.</p></div>
  <div class="abs card" style="left:343px;top:411px"><div class="ico blue"><svg width="30" height="30" viewBox="0 0 24 24" fill="none" stroke="var(--navy)" stroke-width="2"><circle cx="12" cy="4" r="2"/><path d="M11 8v6h5l2 5M8 11a6 6 0 108 8"/></svg></div><h3>Disability Insurance</h3><p>Receive income replacement if you're unable to work due to illness or injury, ensuring financial security.</p></div>
  <div class="abs card" style="left:611px;top:411px"><div class="ico green"><svg width="30" height="30" viewBox="0 0 24 24" fill="var(--green-dark)"><path d="M12 21l-8-8a5 5 0 018-6 5 5 0 018 6z"/></svg></div><h3>Life Insurance</h3><p>Protect your loved ones financially after your passing, covering funeral expenses and ongoing living costs.</p></div>
  <div class="abs card" style="left:879px;top:411px"><div class="ico blue"><svg width="30" height="30" viewBox="0 0 24 24" fill="var(--navy)"><path d="M12 2l8 3v6c0 5-3.5 9-8 11-4.5-2-8-6-8-11V5z"/></svg></div><h3>Health Insurance</h3><p>Cover medical expenses, from check-ups to emergencies, ensuring you get the care you need without financial strain.</p></div>
</section>
<a class="abs btn explore">Explore All <span>↗</span></a>

<h2 class="abs partners-title">OUR PARTNERS</h2>
<div class="abs logo" style="left:244px;top:2338px">Varnix</div>
<div class="abs logo" style="left:427px;top:2338px">Ostle</div>
<div class="abs logo" style="left:611px;top:2338px">Meridale Mutual</div>
<div class="abs logo" style="left:794px;top:2338px">Dunmarrow</div>
<div class="abs logo" style="left:336px;top:2483px">Quillor</div>
<div class="abs logo" style="left:520px;top:2483px">KGZ</div>
<div class="abs logo" style="left:703px;top:2483px">Pellwick</div>

<section class="abs quote">
  <h2>GET A QUOTE TODAY</h2>
  <p>Lorem ipsum dolor sit amet, consectetuer adipiscing elit, sed diam nonummy nibh euismod tincidunt ut laoreet dolore magna aliquam erat volutpat. Ut wisi enim ad minim veniam.</p>
  <a class="btn">Get a Quote <span>↗</span></a>
</section>

<footer class="abs footer">
  <div class="f-col f-about"><h4>BRELLOW COVER INSURANCE</h4><p>Lorem ipsum dolor sit amet, consectetuer adipiscing elit, sed diam nonummy nibh euismod tincidunt utted is laoreet dolore magna aliquam erat volutpat. Ut wisi enim ad minim veniam.<br><a>Read More</a></p></div>
  <div class="f-col" style="left:512px"><h4>Quick Links</h4><ul class="links"><li>Home</li><li>About Us</li><li>Insurance Types</li><li>Contact Us</li><li>Get a Quote</li></ul></div>
  <div class="f-col" style="left:690px"><h4>Follow Us</h4><ul class="social"><li><i></i>Friendwall</li><li><i></i>Vidstream</li><li><i></i>Snapgrid</li><li><i></i>Chirpline</li></ul></div>
  <div class="f-col" style="left:829px"><h4>Contact Details</h4><ul class="contact">
    <li><svg width="12" height="16" viewBox="0 0 12 16" fill="#fff"><path d="M6 0a6 6 0 016 6c0 4.5-6 10-6 10S0 10.5 0 6a6 6 0 016-6zm0 4a2 2 0 100 4 2 2 0 000-4z"/></svg><span>Address<br>123 Building Name,<br>City Name, State XY-123456.</span></li>
    <li><svg width="13" height="13" viewBox="0 0 24 24" fill="#fff"><path d="M6.6 10.8a15 15 0 006.6 6.6l2.2-2.2a1 1 0 011-.25 11.4 11.4 0 003.6.57 1 1 0 011 1V20a1 1 0 01-1 1A17 17 0 013 4a1 1 0 011-1h3.5a1 1 0 011 1c0 1.25.2 2.45.57 3.57a1 1 0 01-.25 1z"/></svg><span>Phone<br>(555) 014-2288</span></li>
    <li><svg width="13" height="11" viewBox="0 0 24 20" fill="#fff"><path d="M2 0h20a2 2 0 012 2v16a2 2 0 01-2 2H2a2 2 0 01-2-2V2a2 2 0 012-2zm10 9L2 3v2l10 6 10-6V3z"/></svg><span>Email<br>info@BrellowCoverInsurance.com</span></li>
  </ul></div>
</footer>
<div class="abs copyright">Copyright © 2025 Brellow Cover Insurance. All Rights Reserved.</div>

</body>
</html>
```